KCA Waltz of our luminaries

My nonprofit social service agency is having a fun gala based on the TV show waltz of the luminaries, and we need the key design for an invitation. The event is a dinner and will have 7 local well-known people dance in a contest-like setting with a nationally known host. This does not need to be the final invitation (RSVP, list of dancers/hosts, etc.). All I need at this point is a great design for the cover to give this event an identity and entice people to attend and/or donate to the cause! Though our logo colors are blue/green/burgandy, this can use black/gold/silver/white as well. Our website is www.kcaohvalley.org if that helps explain who we are.

Also, it can be abstract. And it does not have to include ballroom dancers if the word mark or other graphics are eye catching.

Target Market(s)

Donors, upscale, higher income,45-70, men and women (though women will more likely make the decision to attend)

Industry/Entity Type

Tv

Requirements
Must have
• The wording to be incorporated into the invitation cover is:
Kindred Care Alliance
Celebrates Rising Strong Through Years with
Waltz of the Luminaries
hosted by Host Name (will give the final name when confirmed)

Saturday, November 8, 2014
7 pm
Marlowe Cincinnati Tidewater Court
Nice to have
• I'd like to see something other than ballroom dancers just to give my committee some options. Is it possible to show footprints of dancers (man's shoe with woman's high heels) as the design element? Something that can be used across the invite (rsvp card).
Should not have
• You have free range to create and have fun! If you use our logo colors, either choose one color as the focus, or just be sure to focus on green and burgandy together

```html
<!DOCTYPE html>
<html lang="en">
<head>
<meta charset="utf-8">
<title>Kindred Care Alliance – Waltz of the Luminaries</title>
<link rel="stylesheet" href="https://fonts.googleapis.com/css2?family=Archivo+Black&family=Federant&family=Oswald:wght@400&family=Nunito+Sans:wght@600&display=swap">
<style>
  :root {
    --ink: #0b0a12;
    --night: #05050c;
    --royal: #1f2ed6;
    --violet: #6a1fc4;
    --magenta: #b0208a;
    --teal: #1a7f9a;
    --gold-light: #fff1a8;
    --gold: #e2b93b;
    --gold-deep: #a5781a;
    --cream: #f4e8a8;
    --white: #ffffff;
  }
  html, body {
    margin: 0;
    padding: 0;
    width: 853px;
    height: 1200px;
    overflow: hidden;
    background: var(--night);
  }
  .invitation-cover {
    position: relative;
    width: 853px;
    height: 1200px;
    overflow: hidden;
    background:
      radial-gradient(ellipse 520px 300px at 48% 50%, rgba(255,255,255,0.35), transparent 60%),
      radial-gradient(ellipse 600px 420px at 30% 40%, rgba(31,46,214,0.95), transparent 70%),
      radial-gradient(ellipse 420px 360px at 75% 30%, rgba(106,31,196,0.85), transparent 70%),
      radial-gradient(ellipse 300px 240px at 40% 12%, rgba(176,32,138,0.55), transparent 70%),
      radial-gradient(ellipse 420px 260px at 15% 70%, rgba(106,31,196,0.8), transparent 70%),
      radial-gradient(ellipse 380px 260px at 85% 75%, rgba(26,127,154,0.55), transparent 70%),
      radial-gradient(ellipse 700px 380px at 50% 68%, rgba(31,46,214,0.7), transparent 75%),
      linear-gradient(180deg, var(--ink) 0%, #0d0c3a 30%, #0d0c3a 70%, var(--night) 92%);
  }
  .light-streaks {
    position: absolute;
    inset: 0;
  }
  .brand {
    position: absolute;
    left: 84px;
    top: 46px;
    display: flex;
    align-items: center;
    gap: 14px;
    color: var(--white);
    font-family: "Nunito Sans", sans-serif;
    font-weight: 600;
    font-size: 31px;
    letter-spacing: -0.5px;
  }
  .brand-dot {
    width: 58px;
    height: 58px;
    border-radius: 50%;
    background: var(--white);
  }
  .tagline {
    position: absolute;
    top: 184px;
    left: 0;
    width: 826px;
    text-align: center;
    margin: 0;
    font-family: "Oswald", sans-serif;
    font-weight: 400;
    font-size: 34px;
    line-height: 40px;
    white-space: nowrap;
    color: var(--white);
    letter-spacing: 0.5px;
    text-transform: uppercase;
  }
  .event-title {
    position: absolute;
    left: 100px;
    top: 248px;
    margin: 0;
    font-family: "Archivo Black", sans-serif;
    font-weight: 400;
    line-height: 1;
    text-transform: uppercase;
    white-space: nowrap;
  }
  .event-title span {
    display: block;
    background: linear-gradient(170deg, var(--gold-light) 0%, var(--gold) 35%, var(--gold-deep) 55%, var(--gold-light) 75%, var(--gold) 100%);
    -webkit-background-clip: text;
    background-clip: text;
    color: transparent;
  }
  .title-main { font-size: 134px; letter-spacing: 2px; }
  .title-link { font-size: 50px; margin-top: 4px; letter-spacing: 3px; }
  .title-end { font-size: 78px; margin-top: 6px; letter-spacing: 0; }
  .star {
    position: absolute;
    fill: none;
    stroke: var(--gold);
    stroke-width: 5;
    stroke-linejoin: miter;
  }
  .star-top { left: 680px; top: 50px; width: 98px; height: 98px; }
  .star-mid { left: 492px; top: 384px; width: 66px; height: 66px; }
  .star-low { left: 216px; top: 608px; width: 68px; height: 68px; }
  .dancers {
    position: absolute;
    left: 400px;
    top: 550px;
    width: 400px;
    height: 505px;
    border-radius: 46% 46% 18% 26% / 28% 28% 10% 10%;
    background: linear-gradient(160deg, rgba(255,241,168,0.9) 0%, rgba(226,185,59,0.85) 45%, rgba(165,120,26,0.75) 100%);
  }
  .event-details {
    position: absolute;
    left: 60px;
    top: 788px;
    width: 330px;
    text-align: center;
    font-family: "Federant", serif;
    font-size: 19px;
    line-height: 31px;
    white-space: nowrap;
    color: var(--cream);
    margin: 0;
  }
  .event-details span { display: block; }
  .host-line {
    position: absolute;
    left: 84px;
    top: 1070px;
    margin: 0;
    font-family: "Federant", serif;
    font-size: 22px;
    color: var(--white);
  }
</style>
</head>
<body>
<main class="invitation-cover">
  <svg class="light-streaks" width="853" height="1200" viewBox="0 0 853 1200" aria-hidden="true">
    <g fill="none" stroke-linecap="round">
      <path d="M420 600 Q250 420 60 300" stroke="rgba(120,160,255,0.35)" stroke-width="6"/>
      <path d="M420 600 Q220 520 0 520" stroke="rgba(170,120,255,0.3)" stroke-width="5"/>
      <path d="M420 600 Q260 700 40 900" stroke="rgba(120,200,255,0.25)" stroke-width="5"/>
      <path d="M430 590 Q600 420 820 340" stroke="rgba(150,120,255,0.3)" stroke-width="6"/>
      <path d="M430 600 Q640 640 853 760" stroke="rgba(100,220,220,0.25)" stroke-width="5"/>
      <path d="M420 600 Q400 300 300 60" stroke="rgba(220,80,160,0.25)" stroke-width="8"/>
      <path d="M420 600 Q120 640 0 760" stroke="rgba(190,110,255,0.25)" stroke-width="4"/>
    </g>
  </svg>

  <div class="brand">
    <span class="brand-dot"></span>
    <span class="brand-name">kindred care alliance...</span>
  </div>

  <svg class="star star-top" viewBox="0 0 100 100" aria-hidden="true"><polygon points="50,6 61,38 95,38 67,58 78,92 50,71 22,92 33,58 5,38 39,38"/></svg>

  <p class="tagline">Celebrates Rising Strong Through Years with</p>

  <h1 class="event-title">
    <span class="title-main">Waltz</span>
    <span class="title-link">of the</span>
    <span class="title-end">Luminaries</span>
  </h1>

  <svg class="star star-mid" viewBox="0 0 100 100" aria-hidden="true"><polygon points="50,6 61,38 95,38 67,58 78,92 50,71 22,92 33,58 5,38 39,38"/></svg>
  <svg class="star star-low" viewBox="0 0 100 100" aria-hidden="true"><polygon points="50,6 61,38 95,38 67,58 78,92 50,71 22,92 33,58 5,38 39,38"/></svg>

  <div class="dancers" role="img" aria-label="Gold glittering silhouette of a ballroom dancing couple in a dramatic tango pose"></div>

  <p class="event-details">
    <span>Saturday, November 8, 2014</span>
    <span>7 pm</span>
    <span>Marlowe Cincinnati Tidewater Court</span>
  </p>

  <p class="host-line">hosted by Host Name</p>
</main>
</body>
</html>
```